BOLD & MINIMALIST DESIGN NEEDED

We want a very bold but minimalistic business card design that is impactful and utilizes both sides of the business card. Our current logo is included for your use.

We want bold fonts and good use of negative space. We don't want the logo to overpower the design.

Target Market(s)

Professionals who are building new commercial buildings.

Industry/Entity Type

Construction

Contact Information for Business Card

Name, Title, email, office phone, cell phone, website

Font styles to use
Serif
Sans Serif

Requirements
Must have
• Bold design!

```html
<!DOCTYPE html>
<html lang="en">
<head>
<meta charset="utf-8">
<title>Ridgemont Business Card</title>
<link rel="stylesheet" href="https://fonts.googleapis.com/css2?family=Roboto:wght@300;400;900&display=swap">
<style>
  :root {
    --backdrop: #d9d9d9;
    --ink: #0c0c0d;
    --paper: #ffffff;
    --accent: #7dc242;
    --rule: #8a8a8a;
  }
  html, body {
    margin: 0;
    padding: 0;
    width: 1200px;
    height: 1200px;
    overflow: hidden;
    background: var(--backdrop);
    font-family: "Roboto", Arial, sans-serif;
  }
  .canvas {
    position: relative;
    width: 1200px;
    height: 1200px;
  }
  .card {
    position: absolute;
    left: 261px;
    width: 686px;
    height: 392px;
    overflow: hidden;
    background: var(--paper);
    box-shadow: 0 10px 24px rgba(0,0,0,0.25);
  }
  .card-front { top: 165px; }
  .card-back { top: 653px; }

  /* Front */
  .front-band {
    position: absolute;
    left: 0; top: 0;
    width: 100%;
    height: 219px;
    background: var(--ink);
  }
  .brand {
    position: absolute;
    display: flex;
    align-items: center;
    gap: 14px;
    color: var(--ink);
    font-weight: 900;
    text-transform: uppercase;
    line-height: 1;
    white-space: nowrap;
  }
  .brand-mark {
    display: block;
    background: var(--accent);
  }
  .front-brand {
    left: 50%;
    top: 150px;
    transform: translateX(-50%);
    font-size: 54px;
    letter-spacing: 1px;
    color: var(--paper);
  }
  .front-brand .brand-mark { width: 34px; height: 34px; }
  .front-web {
    position: absolute;
    left: 0; right: 0;
    top: 353px;
    text-align: center;
    font-size: 16px;
    font-weight: 400;
    letter-spacing: 5px;
    color: var(--ink);
  }

  /* Back */
  .back-panel {
    position: absolute;
    left: 0; top: 0;
    width: 343px;
    height: 100%;
    background: #000;
    color: var(--paper);
    font-weight: 300;
  }
  .person-name {
    position: absolute;
    left: 45px; top: 92px;
    margin: 0;
    font-size: 25px;
    font-weight: 300;
    letter-spacing: 0.5px;
    color: var(--accent);
  }
  .name-rule {
    position: absolute;
    left: 0; top: 124px;
    width: 243px;
    height: 1px;
    background: var(--rule);
  }
  .person-title {
    position: absolute;
    left: 45px; top: 129px;
    margin: 0;
    font-size: 16px;
    letter-spacing: 0.5px;
  }
  .address {
    position: absolute;
    left: 45px; top: 190px;
    margin: 0;
    font-style: normal;
    font-size: 16px;
    line-height: 19px;
  }
  .contact-list {
    position: absolute;
    left: 45px; top: 248px;
    margin: 0; padding: 0;
    list-style: none;
    font-size: 16px;
    line-height: 19.5px;
  }
  .contact-list li {
    display: flex;
    align-items: center;
    gap: 10px;
  }
  .contact-icon {
    width: 12px;
    height: 12px;
    flex: none;
    fill: var(--accent);
  }
  .back-brand {
    left: 515px;
    top: 196px;
    transform: translate(-50%, -50%);
    font-size: 34px;
    letter-spacing: 0.5px;
    gap: 10px;
  }
  .back-brand .brand-mark { width: 22px; height: 22px; }
</style>
</head>
<body>
<main class="canvas">

  <section class="card card-front" aria-label="Card front">
    <div class="front-band"></div>
    <div class="brand front-brand"><span class="brand-mark"></span>Ridgemont</div>
    <p class="front-web">www.ridgemont.com</p>
  </section>

  <section class="card card-back" aria-label="Card back">
    <div class="back-panel">
      <h1 class="person-name">Daniel Harper</h1>
      <div class="name-rule"></div>
      <p class="person-title">President</p>
      <address class="address">2140 Alder Court<br>Fairbanks, Alaska 99701</address>
      <ul class="contact-list">
        <li>
          <svg class="contact-icon" viewBox="0 0 12 12" aria-hidden="true"><path d="M2.3 0.5l2 2.2-1 1.4c.7 1.6 2 2.9 3.6 3.6l1.4-1 2.2 2-1.2 2.2C4.6 10.6 1.4 7.4 0.1 1.7z"/></svg>
          555-204-7731
        </li>
        <li>
          <svg class="contact-icon" viewBox="0 0 12 12" aria-hidden="true"><path d="M0 2.5h12v7H0z M0.6 2.8L6 6.6l5.4-3.8" stroke="#000" stroke-width="0.9"/></svg>
          hello@ridgemont.com
        </li>
        <li>
          <svg class="contact-icon" viewBox="0 0 12 12" aria-hidden="true"><circle cx="6" cy="6" r="5.8"/><path d="M3 3.5c1 0 1.6.8 1.4 1.8-.3 1 .8 1.3.6 2.4-.2.8-.9 1.2-1.2 2.1M7.4 1.2c.2 1-.6 1.5.3 2.3.8.7 2 .3 2.6 1.1" stroke="#000" stroke-width="0.8" fill="none"/></svg>
          www.ridgemont.com
        </li>
      </ul>
    </div>
    <div class="brand back-brand"><span class="brand-mark"></span>Ridgemont</div>
  </section>

</main>
</body>
</html>
```